Email Marketing Campaign Brief

We want to do an email marketing campaign around our consulting services. The attached documents provide back ground on our work but additional copy can be found below:

KV7lr is committed to helping you, the educator, make informed buying decisions based on local control and independent reviews through a simple, impartial and an effective approach.
In education, there exists a vast array of educational solutions – such as reading, science, language arts, and math curricula; school-wide reform programs; interventions; after-school programs; and new educational technologies. In the marketplace, providers could, and most do, claim to be able to improve educational outcomes and, in many cases, they all pretend to be supported by evidence. But a cursory review reveals that most evidence consists of poorly designed or advocacy-driven studies with some providers having such inadequate research as could only be described as case studies.

So the problem for State and local education officials is that they must sort through a myriad of such claims to decide which solutions merit consideration for their schools and classrooms. One US official stated the problem saying “many of these practitioners have seen interventions (solutions), introduced with great fanfare as being able to produce dramatic gains, come and go over the years, yielding little in the way of positive and lasting change – a perception confirmed by the flat achievement results over the past 30 years in the Federal Survey of Scholastic Attainment long-term trend”

KV7lr is a process by which we make you, the educator, the locus of control

OUR Approach:
With four simple, yet highly effective steps, KV7lr guides educators through an informed buying process that’s based on local control and review.

Step 1 — Research, Review, and Evaluation Criteria

Step 2 — Cost / Benefit Analysis

Step 3 — Education Survey & Culture Scan

Step 4 — Negotiation & Representation

Target Market(s)

Education

Industry/Entity Type

Marketing

Font styles to use
Sans Serif

Colors
f9b46a
f37122

Requirements
Must have
• HTML format that can be used in an Email Campaign
Nice to have
• Additional Copy in Word

```html
<!DOCTYPE html>
<html lang="en">
<head>
<meta charset="utf-8">
<title>KV7lr – Program Implementation</title>
<link rel="stylesheet" href="https://fonts.googleapis.com/css2?family=Open+Sans:wght@400;600;700;800&family=Roboto+Condensed:wght@400&display=swap">
<style>
  :root {
    --orange: #f37122;
    --orange-soft: #f9b46a;
    --amber: #f8a51d;
    --green-light: #c3ea7a;
    --green-mid: #9fd94e;
    --green-deep: #6fb636;
    --ink: #111111;
    --ink-soft: #3c3c3c;
    --white: #ffffff;
    --grey: #4a4a4a;
  }
  * { margin: 0; padding: 0; box-sizing: border-box; }
  html, body { width: 1200px; height: 1200px; overflow: hidden; background: var(--white); }
  .canvas { position: relative; width: 1200px; height: 1200px; font-family: "Open Sans", Arial, sans-serif; color: var(--ink); }
  .backdrop { position: absolute; inset: 0; }

  .headline { position: absolute; top: 104px; left: 0; width: 1200px; text-align: center; }
  .headline h1 { font-size: 31px; font-weight: 800; letter-spacing: .3px; line-height: 1; }
  .headline p { font-size: 20px; font-weight: 700; margin-top: 10px; }

  .photo { position: absolute; border: 4px solid var(--white); border-radius: 6px; box-shadow: 0 0 0 3px var(--orange), 2px 4px 8px rgba(0,0,0,.35); }
  .photo--children { left: 122px; top: 215px; width: 459px; height: 171px; background: linear-gradient(120deg, #e8b48e, #d94c3a 40%, #5aa7d6 75%, #c9d6e2); }
  .photo--charts { left: 622px; top: 215px; width: 457px; height: 171px; background: linear-gradient(135deg, #f4f4f4, #dcdfe4 60%, #b8bec7); }
  .photo--writing { left: 120px; top: 550px; width: 459px; height: 173px; background: linear-gradient(120deg, #e9e6e1, #f6f5f2 50%, #d9c2b2); }
  .photo--handshake { left: 614px; top: 550px; width: 465px; height: 173px; background: linear-gradient(120deg, #cfd6de, #b89a82 50%, #e8ecef); }

  .step-number { position: absolute; width: 78px; height: 78px; border-radius: 50%; background: var(--white); border: 4px solid var(--orange); color: #e8413c; font-weight: 700; font-size: 46px; line-height: 70px; text-align: center; }

  .step { position: absolute; width: 520px; text-align: center; }
  .step h2 { font-size: 19px; font-weight: 700; line-height: 1.2; margin-bottom: 4px; }
  .step ul { list-style: none; font-family: "Roboto Condensed", Arial, sans-serif; font-size: 13.5px; line-height: 17.5px; }
  .step--1 { left: 85px; top: 434px; }
  .step--2 { left: 582px; top: 434px; }
  .step--3 { left: 85px; top: 764px; }
  .step--4 { left: 582px; top: 764px; }

  .call-to-action { position: absolute; top: 880px; left: 0; width: 1200px; text-align: center; color: var(--grey); }
  .call-to-action .lead { font-size: 28px; font-weight: 400; }
  .call-to-action .brand { color: var(--orange); font-weight: 700; }
  .call-to-action .offer { font-size: 28px; font-weight: 700; margin-top: 2px; }

  .footer { position: absolute; left: 0; top: 986px; width: 1200px; height: 113px; background: var(--orange); border-top: 4px solid var(--orange-soft); color: var(--white); }
  .footer .connect { position: absolute; left: 64px; top: 16px; font-size: 19px; font-weight: 400; }
  .footer .company { position: absolute; left: 64px; top: 46px; font-size: 23px; font-weight: 700; }
  .footer .phone { position: absolute; left: 234px; top: 38px; font-size: 35px; font-weight: 700; }
  .social { position: absolute; right: 94px; top: 17px; display: flex; gap: 12px; }
  .social span { width: 64px; height: 64px; background: var(--white); border-radius: 8px; }

  .web-address { position: absolute; right: 119px; top: 1116px; font-size: 22px; font-weight: 700; color: var(--grey); }
</style>
</head>
<body>
<div class="canvas">
  <svg class="backdrop" width="1200" height="1200" viewBox="0 0 1200 1200" aria-hidden="true">
    <defs>
      <linearGradient id="sky" x1="0" y1="0" x2="0" y2="1">
        <stop offset="0" stop-color="#8fcd3f"/>
        <stop offset="1" stop-color="#d2f08f"/>
      </linearGradient>
    </defs>
    <!-- top green field -->
    <rect x="0" y="0" width="1200" height="420" fill="url(#sky)"/>
    <path d="M0 0 H1200 V30 Q1050 5 900 28 Q760 8 600 32 Q430 5 260 30 Q120 8 0 28 Z" fill="var(--green-deep)"/>
    <path d="M0 28 Q120 8 260 30 Q430 5 600 32 Q760 8 900 28 Q1050 5 1200 30 V60 Q1000 40 800 62 Q600 42 400 60 Q200 40 0 58 Z" fill="var(--green-mid)"/>
    <!-- orange band, torn edges -->
    <path d="M0 186 L40 180 L70 190 L120 178 L160 188 L210 180 L260 192 L310 181 L370 190 L420 179 L480 189 L540 182 L600 192 L660 180 L720 190 L780 181 L840 191 L900 179 L960 189 L1020 180 L1080 191 L1140 181 L1200 188 V402 L1150 408 L1100 398 L1040 410 L980 400 L920 409 L860 398 L800 406 L740 397 L680 409 L620 399 L560 408 L500 397 L440 407 L380 398 L320 409 L260 400 L200 408 L140 397 L80 407 L30 399 L0 405 Z" fill="var(--orange)"/>
    <!-- light green middle band -->
    <path d="M0 405 L30 399 L80 407 L140 397 L200 408 L260 400 L320 409 L380 398 L440 407 L500 397 L560 408 L620 399 L680 409 L740 397 L800 406 L860 398 L920 409 L980 400 L1040 410 L1100 398 L1150 408 L1200 402 V540 H0 Z" fill="var(--green-light)"/>
    <!-- amber band -->
    <path d="M0 528 L50 522 L100 532 L160 521 L220 530 L280 523 L340 533 L400 522 L460 531 L520 521 L580 532 L640 523 L700 531 L760 521 L820 532 L880 522 L940 531 L1000 521 L1060 532 L1120 523 L1200 530 V728 L1150 738 L1090 727 L1030 740 L970 729 L910 739 L850 727 L790 738 L730 728 L670 740 L610 729 L550 739 L490 727 L430 738 L370 728 L310 739 L250 727 L190 738 L130 728 L70 739 L0 729 Z" fill="var(--amber)"/>
    <rect x="0" y="738" width="1200" height="248" fill="var(--white)"/>
    <path d="M0 729 L70 739 L130 728 L190 738 L250 727 L310 739 L370 728 L430 738 L490 727 L550 739 L610 729 L670 740 L730 728 L790 738 L850 727 L910 739 L970 729 L1030 740 L1090 727 L1150 738 L1200 728 V745 H0 Z" fill="var(--white)"/>
  </svg>

  <header class="headline">
    <h1>PROGRAM IMPLEMENTATION</h1>
    <p>Independent Review Connected to School District Need and Stakeholder</p>
  </header>

  <div class="photo photo--children" role="img" aria-label="Photo of smiling school children"></div>
  <div class="photo photo--charts" role="img" aria-label="Photo of printed charts with a pen"></div>
  <div class="photo photo--writing" role="img" aria-label="Photo of a hand writing on a survey form"></div>
  <div class="photo photo--handshake" role="img" aria-label="Photo of two professionals shaking hands"></div>

  <div class="step-number" style="left:310px; top:354px;">1</div>
  <div class="step-number" style="left:810px; top:356px;">2</div>
  <div class="step-number" style="left:310px; top:682px;">3</div>
  <div class="step-number" style="left:810px; top:682px;">4</div>

  <section class="step step--1">
    <h2>Research, Review,and Evaluation Criteria</h2>
    <ul>
      <li>* District needs analysis</li>
      <li>* Program reviews and alignment to need</li>
      <li>* Independent evaluation / data informed decisions</li>
    </ul>
  </section>
  <section class="step step--2">
    <h2>Cost / Benefit Analysis</h2>
    <ul>
      <li>* Cost alignment based on research, review and evaluation of programs</li>
      <li>* Program cost by product offering and alignment to identified needs</li>
      <li>* Sumary of cost, data and return on investment</li>
    </ul>
  </section>
  <section class="step step--3">
    <h2>Education Survey and Culture Scan</h2>
    <ul>
      <li>* District observation and perception survey</li>
      <li>* Culture scan to identify education best practices</li>
      <li>* Match to strategic plan goals and objectives</li>
    </ul>
  </section>
  <section class="step step--4">
    <h2>Negotiation and Representation</h2>
    <ul>
      <li>* Conduct Provider review and presentation</li>
      <li>* Representation for content and program negotiations</li>
      <li>* Support district in independent decision-marketing process</li>
    </ul>
  </section>

  <div class="call-to-action">
    <p class="lead">Let <span class="brand">KV7lr</span> help you make informed buying decisions.</p>
    <p class="offer">Contact us today for a no-cost consultation</p>
  </div>

  <footer class="footer">
    <span class="connect">Let’s get connected!</span>
    <span class="company">KV7lr, LLC</span>
    <span class="phone">555.204.7781</span>
    <div class="social" aria-label="Social links">
      <span></span><span></span><span></span><span></span>
    </div>
  </footer>

  <p class="web-address">www.KV7lr.com</p>
</div>
</body>
</html>
```